Brightmill Data Works

Our company is about IT hardwares and IT solutions. IT hardware such as PC, RAMS, storage and servers. IT solutions such as project management, BA. We are also selling new technology too.

Target Market(s)

Consumer, Small to Medium Business, Corporate

Requirements
Must have
• The business card must have the following:
• Name:
• Title:
• Contact Number:
• Email address:
• Website:
• Color: Must match the logo color upgrade

```html
<!DOCTYPE html>
<html lang="en">
<head>
<meta charset="utf-8">
<title>Brightmill Data Works — Business Card</title>
<link href="https://fonts.googleapis.com/css2?family=Open+Sans:wght@400;600;700&display=swap" rel="stylesheet">
<style>
  :root {
    --backdrop: #3b3b3c;
    --paper: #efefef;
    --ink: #4a4a4a;
    --ink-soft: #5c5c5c;
    --rule: #c9c9c9;
    --accent: #d9781f;
    --night: #0e0e0e;
    --white: #ffffff;
  }
  * { box-sizing: border-box; margin: 0; padding: 0; }
  html, body { width: 1200px; height: 896px; overflow: hidden; }
  body {
    background: var(--backdrop);
    font-family: "Open Sans", Arial, sans-serif;
    position: relative;
  }
  .card {
    position: absolute;
    left: 267px;
    width: 666px;
    height: 380px;
    box-shadow: 0 10px 28px rgba(0,0,0,.45);
  }
  .card--front { top: 48px; background: var(--paper); }
  .card--back  { top: 468px; background: var(--night); }

  /* front */
  .holder {
    position: absolute; left: 56px; top: 72px; width: 340px;
  }
  .holder__name {
    color: var(--accent); font-weight: 700; font-size: 20px;
    letter-spacing: .04em; text-transform: uppercase; line-height: 1.3;
  }
  .holder__title {
    color: var(--ink-soft); font-size: 16px; line-height: 1.3;
  }
  .holder__rule {
    height: 1px; background: var(--rule); margin-top: 10px; margin-left: 120px; width: 220px;
  }
  .brand {
    position: absolute; right: 52px; top: 160px;
    display: flex; align-items: center; gap: 12px;
  }
  .brand__dot {
    width: 20px; height: 20px; border-radius: 50%; background: var(--accent);
  }
  .brand__name {
    color: var(--ink); font-weight: 700; font-size: 26px;
    letter-spacing: .03em; text-transform: uppercase; line-height: 1;
  }
  .contact-rule {
    position: absolute; right: 52px; top: 236px; width: 300px; height: 1px; background: var(--rule);
  }
  .contacts {
    position: absolute; right: 52px; top: 250px; list-style: none; text-align: right;
  }
  .contacts li {
    display: flex; justify-content: flex-end; align-items: center; gap: 10px;
    color: var(--ink); font-size: 16px; line-height: 26px;
  }
  .contacts svg { width: 14px; height: 14px; flex: none; }

  /* back */
  .back-brand {
    position: absolute; left: 0; right: 0; top: 140px; text-align: center;
  }
  .back-brand__name {
    color: var(--white); font-weight: 700; font-size: 38px;
    letter-spacing: .04em; text-transform: uppercase; line-height: 1.1;
  }
  .back-brand__tagline {
    color: var(--white); font-size: 14px; letter-spacing: .06em;
    text-transform: uppercase; margin-top: 22px;
  }
</style>
</head>
<body>

<section class="card card--front" aria-label="Business card front">
  <div class="holder">
    <p class="holder__name">Daniel Reyes</p>
    <p class="holder__title">Managing Director</p>
    <div class="holder__rule"></div>
  </div>

  <div class="brand">
    <span class="brand__dot"></span>
    <span class="brand__name">Brightmill Data Works</span>
  </div>

  <div class="contact-rule"></div>
  <ul class="contacts">
    <li>044-555 010 482
      <svg viewBox="0 0 16 16" aria-hidden="true"><path fill="var(--accent)" d="M3 2h3l1.5 3.5-2 1.3a8 8 0 0 0 3.7 3.7l1.3-2L14 10v3a1 1 0 0 1-1 1A11 11 0 0 1 2 3a1 1 0 0 1 1-1z"/></svg>
    </li>
    <li>info@brightmill.com
      <svg viewBox="0 0 16 16" aria-hidden="true"><rect x="1" y="3" width="14" height="10" rx="1" fill="var(--accent)"/><path d="M2 4l6 5 6-5" stroke="#fff" stroke-width="1.3" fill="none"/></svg>
    </li>
    <li>www.brightmilldata.com
      <svg viewBox="0 0 16 16" aria-hidden="true"><circle cx="8" cy="8" r="7" fill="var(--accent)"/><path d="M1 8h14M8 1c-3 3.5-3 10.5 0 14M8 1c3 3.5 3 10.5 0 14" stroke="#fff" stroke-width="1" fill="none"/></svg>
    </li>
  </ul>
</section>

<section class="card card--back" aria-label="Business card back">
  <div class="back-brand">
    <p class="back-brand__name">Brightmill Data Works</p>
    <p class="back-brand__tagline">IT Hardwares and IT Solutions</p>
  </div>
</section>

</body>
</html>
```